I need a business card designed using the logo provided either vertical or horizontal......Harbourline Property Group is an Australian based real estate company that caters for the upper end of the market so the design of the business card "must reflect" the companies image!!
Colour combinations are optional but "must be realistic" and must be able to be accurately useable CMYK colours.
Please consider that any colours used "must be able to be used" and be suitable in following designs for "pull out banner signs" and "real estate signs".
The colours and the font in the attached designs are for example and other combinations are encouraged.
Target Market(s)
The High End of the Australian real estate market
Industry/Entity Type
Business
Contact Information for Business Card
Logo - Business Name - Director + Licensed Real Estate Agent - Mobile Number (Cell Phone) - Business Number - Fax - Email Address - Web address
Requirements
Must have
- Designs and colours (CMYK) that can easily be interpreted by an Australian printer.
Nice to have
- Some alternative ideas on colour and font..........the ones provided are ok and have been provided as an example but I am looking for alternative ideas
Should not have
- Loud, overly bright colours. Designs that do not reflect the professional standards of the business.
- Designs that look good on a computer monitor but can not be re-created on a printing press.............this is most important when it comes to shading etc.

```html
<!DOCTYPE html>
<html lang="en">
<head>
<meta charset="utf-8">
<title>Harbourline Property Group — Business Card</title>
<link rel="stylesheet" href="https://fonts.googleapis.com/css2?family=Michroma&family=Open+Sans:wght@400;600&display=swap">
<style>
  :root {
    --backdrop: #e4e4e4;
    --card-white: #f4f4f4;
    --ink: #1f1d1e;
    --gold: #a87a2a;
    --sand: #c2b488;
    --light: #f2f2f2;
  }
  * { box-sizing: border-box; margin: 0; padding: 0; }
  html, body { width: 1200px; height: 1192px; overflow: hidden; }
  body {
    background: var(--backdrop);
    font-family: "Open Sans", sans-serif;
    display: flex;
    flex-direction: column;
    align-items: center;
    justify-content: center;
    gap: 60px;
  }
  .card {
    position: relative;
    width: 760px;
    height: 434px;
    background: var(--card-white);
    box-shadow: 0 6px 18px rgba(0,0,0,0.12);
    overflow: hidden;
  }

  /* Back side */
  .card-back .brand-mark {
    position: absolute;
    left: 70px;
    top: 90px;
    display: flex;
    align-items: center;
    gap: 16px;
  }
  .brand-square {
    width: 22px;
    height: 22px;
    background: var(--gold);
  }
  .brand-name {
    font-family: "Michroma", sans-serif;
    color: var(--ink);
    text-transform: uppercase;
    letter-spacing: 3px;
  }
  .card-back .brand-name { font-size: 26px; }

  /* Front side */
  .front-top {
    height: 140px;
    display: flex;
    align-items: flex-end;
    justify-content: center;
    padding-bottom: 22px;
  }
  .card-front .brand-name { font-size: 17px; }
  .front-band {
    position: absolute;
    left: 0; right: 0; bottom: 0;
    height: 294px;
    background: var(--ink);
    color: var(--light);
    padding: 24px 40px 0;
  }
  .holder {
    text-align: center;
    margin-bottom: 26px;
  }
  .holder-name {
    font-family: "Michroma", sans-serif;
    font-size: 17px;
    letter-spacing: 4px;
    text-transform: uppercase;
    color: var(--light);
  }
  .holder-title {
    font-family: "Michroma", sans-serif;
    font-size: 11px;
    letter-spacing: 3px;
    text-transform: uppercase;
    color: var(--gold);
    margin-top: 6px;
  }
  .contact-grid {
    display: grid;
    grid-template-columns: 300px 1fr;
    column-gap: 20px;
  }
  .company-line {
    font-family: "Michroma", sans-serif;
    font-size: 10px;
    letter-spacing: 2px;
    text-transform: uppercase;
    color: var(--gold);
    margin-bottom: 14px;
  }
  .contact-list { list-style: none; }
  .contact-list li {
    display: flex;
    align-items: center;
    gap: 14px;
    font-size: 15px;
    letter-spacing: 0.5px;
    line-height: 1;
    margin-bottom: 14px;
  }
  .contact-list svg { width: 16px; height: 16px; flex: none; }
  .contact-list.right { padding-top: 0; }
  .contact-list .no-icon { padding-left: 30px; }
</style>
</head>
<body>

<section class="card card-back" aria-label="Card back">
  <div class="brand-mark">
    <span class="brand-square"></span>
    <span class="brand-name">Harbourline Property Group</span>
  </div>
</section>

<section class="card card-front" aria-label="Card front">
  <div class="front-top">
    <span class="brand-name">Harbourline Property Group</span>
  </div>
  <div class="front-band">
    <div class="holder">
      <p class="holder-name">Marcus Ellery</p>
      <p class="holder-title">CEO</p>
    </div>
    <div class="contact-grid">
      <div>
        <p class="company-line">Harbourline Property Group</p>
        <ul class="contact-list">
          <li>
            <svg viewBox="0 0 16 16" aria-hidden="true"><rect x="4" y="1" width="8" height="14" rx="1.5" fill="none" stroke="#a87a2a" stroke-width="1.4"/><line x1="7" y1="12.5" x2="9" y2="12.5" stroke="#a87a2a" stroke-width="1.4"/></svg>
            +61 412 555 019
          </li>
          <li>
            <svg viewBox="0 0 16 16" aria-hidden="true"><path d="M2 7 Q8 1 14 7 L12 9 L10 7.5 L6 7.5 L4 9 Z" fill="none" stroke="#a87a2a" stroke-width="1.3"/><rect x="4" y="9" width="8" height="5" fill="none" stroke="#a87a2a" stroke-width="1.3"/></svg>
            +61 2 5550 1842
          </li>
        </ul>
      </div>
      <ul class="contact-list right">
        <li class="no-icon">18 Wharf Lane, Darling Point, Sydney.</li>
        <li>
          <svg viewBox="0 0 16 16" aria-hidden="true"><rect x="1.5" y="3.5" width="13" height="9" fill="none" stroke="#a87a2a" stroke-width="1.3"/><path d="M1.5 3.5 L8 9 L14.5 3.5" fill="none" stroke="#a87a2a" stroke-width="1.3"/></svg>
          marcus@harbourlinegroup.com.au
        </li>
        <li>
          <svg viewBox="0 0 16 16" aria-hidden="true"><circle cx="8" cy="8" r="6.5" fill="none" stroke="#a87a2a" stroke-width="1.3"/><ellipse cx="8" cy="8" rx="3" ry="6.5" fill="none" stroke="#a87a2a" stroke-width="1.1"/><line x1="1.5" y1="8" x2="14.5" y2="8" stroke="#a87a2a" stroke-width="1.1"/></svg>
          www.harbourlinegroup.com.au
        </li>
      </ul>
    </div>
  </div>
</section>

</body>
</html>
```